Kesso Tea Premium Matcha brand Label

This is a label design project for a luxury tea brand. Feel free to be creative within the guidelines.
Attached to this project is a document called “Private Label Design Requirements” with the design guidelines and template. There is another document called "Kesso Tea Packaging Instructions" this has more details necessary to stick to the guidelines in the first document.

I have also attached the certifications to be included as well as different variations of the logo for you to use.

If you have any questions, I am here.
Updates

Need extra days to review

Target Market(s)

Young, active, fun, enjoy the finer things

```html
<!DOCTYPE html>
<html lang="en">
<head>
<meta charset="utf-8">
<title>Kesso Tea Ceremonial Matcha Label</title>
<link href="https://fonts.googleapis.com/css2?family=Raleway:wght@500;600;700;800&display=swap" rel="stylesheet">
<style>
  :root {
    --backdrop: #bfcab8;
    --lime: #c5d862;
    --lime-line: #a9c94c;
    --leaf-deep: #2f6a1c;
    --leaf-mid: #4e8f2c;
    --band: #6dba45;
    --title-green: #6cbf3f;
    --frame: #3d5a24;
    --ink: #1e1e1e;
    --white: #ffffff;
    --heading-lime: #a8d13a;
  }
  * { margin: 0; padding: 0; box-sizing: border-box; }
  html, body { width: 1200px; height: 803px; overflow: hidden; }
  body {
    background: var(--backdrop);
    font-family: "Raleway", sans-serif;
    position: relative;
  }
  .label {
    position: absolute;
    left: 52px; top: 295px;
    width: 1097px; height: 212px;
    background: var(--lime);
    box-shadow: 0 8px 14px rgba(0,0,0,0.18);
    overflow: hidden;
  }
  .label-shapes { position: absolute; inset: 0; }
  .front-panel {
    position: absolute;
    left: 460px; top: 18px;
    width: 177px; height: 176px;
    background: var(--white);
    padding: 18px;
  }
  .front-frame {
    width: 100%; height: 100%;
    border: 2px solid var(--frame);
    display: flex; flex-direction: column; align-items: center;
    text-align: center;
  }
  .brand-name {
    margin-top: 40px;
    font-weight: 800;
    font-size: 16px;
    color: var(--ink);
    letter-spacing: 0.3px;
  }
  .product-name {
    margin-top: 8px;
    font-weight: 700;
    font-size: 11.2px;
    line-height: 1.25;
    color: var(--title-green);
  }
  .net-weight {
    margin-top: auto;
    margin-bottom: 5px;
    font-weight: 600;
    font-size: 7.5px;
    color: var(--ink);
  }
  .company-info {
    position: absolute;
    left: 79px; top: 132px;
    color: var(--white);
    font-weight: 700;
    font-size: 9.3px;
    line-height: 1.3;
  }
  .product-info {
    position: absolute;
    left: 798px; top: 51px;
    color: var(--white);
    font-weight: 700;
  }
  .info-heading {
    color: var(--heading-lime);
    font-size: 11.5px;
    font-weight: 600;
  }
  .info-text { font-size: 9.4px; margin: 4px 0 7px 8px; }
  .steps { list-style: none; margin: 3px 0 0 8px; font-size: 9.4px; line-height: 1.27; }
  .steps li::before { content: "\2022\00a0"; font-size: 7px; vertical-align: 1px; }
  .cert-badges { position: absolute; left: 953px; top: 143px; display: flex; gap: 6px; }
  .badge-round { width: 31px; height: 31px; border-radius: 50%; background: var(--white); border: 3px solid var(--leaf-deep); }
  .badge-square { width: 35px; height: 26px; margin-top: 3px; background: #2e7cb8; border: 2px solid var(--white); }
</style>
</head>
<body>
  <div class="label">
    <svg class="label-shapes" width="1097" height="212" viewBox="0 0 1097 212">
      <defs>
        <linearGradient id="leafTone" x1="0" y1="0" x2="1" y2="1">
          <stop offset="0" stop-color="#3f7f24"/>
          <stop offset="0.5" stop-color="#4e9030"/>
          <stop offset="1" stop-color="#2d6a1b"/>
        </linearGradient>
      </defs>
      <rect class="wave-field" width="1097" height="212" fill="var(--lime)" role="img" aria-label="Overlapping arch pattern in lime green"/>
      <path class="band-left" d="M0 0 H250 C330 50 350 150 268 212 H0 Z" fill="var(--band)"/>
      <path class="leaves-left" d="M0 0 H243 C320 50 335 150 250 212 H0 Z" fill="url(#leafTone)" role="img" aria-label="Photograph of fresh green tea leaves"/>
      <path class="band-right" d="M1097 0 H858 C780 50 760 150 838 212 H1097 Z" fill="var(--band)"/>
      <path class="leaves-right" d="M1097 0 H866 C790 50 776 150 848 212 H1097 Z" fill="url(#leafTone)" role="img" aria-label="Photograph of fresh green tea leaves"/>
    </svg>

    <div class="company-info">
      <p>Distributed by Kesso Tea Co. | Maple Falls, Ga</p>
      <p>Certified Organic by orvea</p>
      <p>PRODUCT OF JAPAN</p>
    </div>

    <div class="front-panel">
      <div class="front-frame">
        <p class="brand-name">Kesso Tea</p>
        <h1 class="product-name">PREMIUM ORGANIC<br>CEREMONIAL MATCHA</h1>
        <p class="net-weight">Net Wt: 30g</p>
      </div>
    </div>

    <div class="product-info">
      <h2 class="info-heading">Ingredients</h2>
      <p class="info-text">Premium Organic Japanese Matcha Green Tea</p>
      <h2 class="info-heading">Instructions</h2>
      <ul class="steps">
        <li>2 tsp of Matcha</li>
        <li>2oz of Water (170-180 degrees F)</li>
        <li>Whisk in a W formation until frothy</li>
        <li>Sweeten to taste</li>
      </ul>
    </div>

    <div class="cert-badges">
      <div class="badge-round"></div>
      <div class="badge-square"></div>
    </div>
  </div>
</body>
</html>
```